Innovation Company Business Card Design

I need to have my business card updated. The current card was designed when the company started 2.5 years ago and was a quick and dirty job.

I need a new card design that is more professional and has my updated company tag line.

I will include the old card's Corel Draw file, and EPS versions as examples of the current design. I will also include the company logo eps and corel version files.

The company pantone colour is pantone 1805 c (a dark red)

I want the design to convey the nature of our business as a strategic technology innovation company, but yet still be professional. We are funky vibey and work from an industrial style office in a vibey designer dominat part of town. Though are clients include large banks and corporate clients too.

The information that needs to be on the card is in attached word document (but doesn't have to be in this order or format)

Final version needs to be supplied in PNG preview, as well as PSD file format (or other editable file version) so that personal information on card can be easily edited and reprinted.

Target Market(s)

CEO's of small to medium size companies
Marketing Managers of large coporates
Account managers of Digital Agencies

Industry/Entity Type

Business

Requirements
Must have
• 86x54mm will be cut in rounded corner credit card size format (Except if you recommend otherwise in your design)
Nice to have
• Some kind of background transparency combined with the pantone colour that gives the card some dimension and depth. But no gradient fills please :-)
Should not have
• Basic gradient fills
• Clipart

```html
<!DOCTYPE html>
<html lang="en">
<head>
<meta charset="utf-8">
<title>Velorix Business Card</title>
<link rel="stylesheet" href="https://fonts.googleapis.com/css2?family=Arimo:wght@400;700&display=swap">
<style>
  :root {
    --brand-red: #b3232a;
    --brand-red-dark: #a41e24;
    --paper: #ffffff;
    --ink: #1c1c1c;
    --backdrop: #e4e5e7;
    --rule: #2a2a2a;
  }
  * { margin: 0; padding: 0; box-sizing: border-box; }
  html, body {
    width: 1200px;
    height: 900px;
    overflow: hidden;
    background: var(--backdrop);
    font-family: "Arimo", Arial, sans-serif;
  }
  .sheet {
    position: relative;
    width: 1200px;
    height: 900px;
  }
  .card {
    position: absolute;
    left: 320px;
    width: 560px;
    height: 352px;
    border-radius: 26px;
    overflow: hidden;
  }

  /* Front */
  .card-front {
    top: 66px;
    background: var(--brand-red);
    color: var(--paper);
  }
  .front-brand {
    position: absolute;
    left: 60px;
    top: 104px;
    width: 360px;
  }
  .front-brand .wordmark {
    font-weight: 700;
    font-size: 76px;
    line-height: 1;
    letter-spacing: -1px;
  }
  .front-brand .tagline {
    margin-top: 6px;
    text-align: right;
    font-size: 15px;
    padding-right: 62px;
  }
  .web-bar {
    position: absolute;
    left: 60px;
    right: 44px;
    top: 258px;
    height: 24px;
    background: var(--paper);
    color: var(--brand-red);
    font-size: 12px;
    letter-spacing: 7px;
    line-height: 24px;
    padding-left: 36px;
  }

  /* Back */
  .card-back {
    top: 466px;
    background: var(--paper);
    color: var(--ink);
  }
  .brand-square {
    position: absolute;
    left: 56px;
    top: 106px;
    width: 112px;
    height: 112px;
    background: var(--brand-red);
  }
  .divider {
    position: absolute;
    left: 206px;
    top: 52px;
    width: 1.5px;
    height: 168px;
    background: var(--rule);
  }
  .contact {
    position: absolute;
    left: 224px;
    top: 50px;
    font-size: 12.5px;
    line-height: 1.3;
  }
  .contact .person-name {
    color: var(--brand-red);
    font-weight: 700;
    font-size: 17px;
  }
  .contact .role { margin-bottom: 12px; }
  .contact .label { color: var(--brand-red); }
  .contact .lines { margin-bottom: 12px; }
  .contact .company {
    color: var(--brand-red);
    font-weight: 700;
    font-size: 13.5px;
  }
  .band {
    position: absolute;
    left: 0;
    bottom: 0;
    width: 560px;
    height: 352px;
  }
  .band-name {
    position: absolute;
    left: 22px;
    top: 248px;
    font-weight: 700;
    font-size: 104px;
    line-height: 1;
    color: var(--paper);
    letter-spacing: -2px;
    transform: rotate(-6deg);
    transform-origin: left top;
  }
</style>
</head>
<body>
<main class="sheet">

  <section class="card card-front" aria-label="Business card front">
    <div class="front-brand">
      <div class="wordmark">Velorix</div>
      <div class="tagline">Strategic Innovation</div>
    </div>
    <div class="web-bar">www.velorix.com</div>
  </section>

  <section class="card card-back" aria-label="Business card back">
    <svg class="band" viewBox="0 0 560 352" aria-hidden="true">
      <polygon points="0,286 560,216 560,352 0,352" fill="var(--brand-red)"/>
    </svg>
    <div class="brand-square" aria-hidden="true"></div>
    <div class="divider" aria-hidden="true"></div>
    <div class="contact">
      <div class="person-name">Daniel Hartley</div>
      <div class="role">Founder &amp; MD</div>
      <div class="lines">
        <div>daniel@velorix.com</div>
        <div><span class="label">mobile:</span> 0831234567 &nbsp;<span class="label">office:</span> 010 555 0142</div>
      </div>
      <div class="company">Velorix (Pty) Ltd</div>
      <div>Suite 210, 14 Marula Rd. Parkview,</div>
      <div>JHB, RSA</div>
    </div>
    <div class="band-name">Velorix</div>
  </section>

</main>
</body>
</html>
```